Luxury Toilet Rental Business. Tallowby Hire.

Tallowby Hire (the logo is in the uploaded files)
We RENT and SELL Luxury Trailer toilets.
- Show location, number, pricing, pictures.
- We have two stall trailers for rent AND 3 stall trailers
- We sell them too
- We want our phone number shown
- We are a local company
- Slogan: Brighten your gathering with Tallowby Hire. The Velvet Privy
- We want a pricing portion
- We want the sizes shown
- We want the different rates/ prices shown
- We do 1 day rentals
- We do 1 week rentals
- We want the service area. We serve Los Angeles County, Orange County, Riverside County, San Bernardino County, and Palm Desert.
- Our location is in Santa Ana California

Target Market(s)

Event planners, wedding planners, venue planners, concerts, events, gatherings.

Industry/Entity Type

Luxury Toilet Rentals

Number of Pages Required

1 page

Font styles to use
Serif
Sans Serif

Colors
EE7325
F08F49
F5BC92
FAE3D3
FDF4ED

Requirements
Must have
• Location, pricing, pictures, available areas. Our slogan.
Nice to have
• I like the idea of having tabs that show price, a tab that shows our contact information, pictures, event ideas, and where we service (the areas we'll go to)

```html
<!DOCTYPE html>
<html lang="en">
<head>
<meta charset="utf-8">
<title>Tallowby Hire — Luxury Toilet Trailer Rentals</title>
<link rel="stylesheet" href="https://fonts.googleapis.com/css2?family=Poppins:ital,wght@0,300;0,400;0,500;0,600;1,400;1,500&display=swap">
<style>
:root{
  --orange:#EE7325;
  --orange-soft:#F08F49;
  --peach:#F5BC92;
  --cream:#FAE3D3;
  --blush:#FDF4ED;
  --ink:#2f2f2f;
  --muted:#7a7a7a;
  --white:#ffffff;
}
*{box-sizing:border-box;margin:0;padding:0}
html,body{width:1200px;height:4236px;overflow:hidden}
body{position:relative;background:var(--white);font-family:'Poppins',sans-serif;color:var(--ink)}
.abs{position:absolute}
a{color:inherit;text-decoration:none}

/* nav */
.nav{left:0;top:0;width:1200px;height:100px;background:var(--white)}
.brand{left:94px;top:34px;display:flex;align-items:center;gap:8px;font-weight:600;font-size:20px;color:var(--orange)}
.brand-square{width:14px;height:14px;background:var(--orange)}
.menu{left:352px;top:34px;display:flex;gap:28px;font-size:18px}
.menu .active{text-decoration:underline;text-underline-offset:5px;font-weight:500}
.login{left:983px;top:23px;width:132px;height:48px;border-radius:24px;background:var(--orange-soft);color:var(--white);font-weight:600;font-size:18px;display:flex;align-items:center;justify-content:center}

/* hero */
.hero{left:0;top:100px;width:1200px;height:574px;background:linear-gradient(180deg,#3e3b36 0%,#4a4640 45%,#2e2d2b 100%)}
.hero-title{left:0;top:244px;width:1200px;text-align:center;font-size:35px;font-weight:600;color:var(--white)}
.hero-sub{left:180px;top:300px;width:840px;text-align:center;font-size:19.5px;line-height:30px;color:var(--white)}
.btn{height:46px;border-radius:23px;font-weight:600;font-size:17px;display:flex;align-items:center;justify-content:center;color:var(--white)}
.btn-fill{left:411px;top:403px;width:151px;background:var(--orange-soft)}
.btn-line{left:618px;top:403px;width:171px;border:2px solid var(--orange-soft)}

/* headings */
.sec-title{left:0;width:1200px;text-align:center;font-size:29px;font-weight:500}
.sec-sub{left:300px;width:600px;text-align:center;font-size:19px;line-height:29px;color:var(--muted)}

/* areas */
.area{top:884px;width:179px;height:178px;border-radius:12px;background:var(--orange-soft);color:var(--white);font-weight:600;font-size:20px;line-height:30px;display:flex;align-items:center;justify-content:center;text-align:center;padding:0 18px}
.area.raised{box-shadow:0 12px 18px rgba(0,0,0,.16)}

/* rentals */
.rental-band{left:0;top:1131px;width:1200px;height:746px;background:radial-gradient(ellipse at 50% 12%,var(--cream) 0%,var(--blush) 55%,var(--blush) 100%)}
.rental-card{top:1378px;width:473px;height:447px;background:var(--white);border-radius:16px;overflow:hidden;box-shadow:0 10px 18px rgba(0,0,0,.12)}
.photo{display:block;width:100%}
.rental-card .photo{height:220px;background:linear-gradient(180deg,#9ea3a8 0%,#7e7f7c 55%,#5f5f5d 100%)}
.rc-head{position:absolute;left:20px;right:20px;top:250px;display:flex;justify-content:space-between;font-size:21px}
.rc-head .price{font-size:24px;font-weight:500}
.rc-row{position:absolute;left:20px;display:flex;align-items:center;gap:16px;font-size:16px}
.rc-more{position:absolute;left:0;width:100%;top:402px;text-align:center;color:var(--orange);font-size:20px;font-weight:500}

/* products */
.product{top:2094px;width:316px;height:439px;background:var(--orange-soft);border-radius:16px;overflow:hidden;color:var(--white)}
.product.raised{box-shadow:0 12px 18px rgba(0,0,0,.18)}
.product .photo{height:219px;background:linear-gradient(180deg,#e4e4e2 0%,#cfcfcc 100%)}
.product .photo.warm{background:linear-gradient(90deg,#9a9894 0%,#c7c4bf 45%,#a8804f 75%,#8a6a45 100%)}
.pd-head{position:absolute;left:20px;right:20px;top:248px;display:flex;justify-content:space-between;font-size:23px;font-weight:600}
.pd-sub{position:absolute;left:20px;top:290px;font-size:16px}
.pd-phone{position:absolute;left:20px;top:329px;display:flex;align-items:center;gap:12px;font-size:16px}
.pd-cta{position:absolute;left:0;width:100%;top:396px;text-align:center;font-size:18px;font-weight:600}

/* about */
.about-photo{left:84px;top:2701px;width:480px;height:460px;border-radius:16px;background:linear-gradient(135deg,#3a3a3a 0%,#8a8a86 45%,#e6e6e3 75%,#cfcfcc 100%)}
.about-title{left:597px;top:2736px;font-size:31px;font-weight:500}
.about-text{left:597px;top:2790px;width:520px;font-size:19px;line-height:30px;color:var(--muted)}
.tick-row{left:597px;display:flex;align-items:center;gap:22px;font-size:19px;color:var(--muted)}

/* testimonials */
.review{top:3308px;width:316px;height:327px;background:var(--orange-soft);border-radius:12px;color:var(--white)}
.avatar{position:absolute;left:24px;top:34px;width:66px;height:66px;border-radius:50%;background:linear-gradient(135deg,#6a6f72,#c9ccce)}
.rv-name{position:absolute;left:108px;top:50px;font-size:23px;font-weight:600}
.rv-quote{position:absolute;left:24px;top:116px;width:272px;font-style:italic;font-size:20px;line-height:30px}
.rv-time{position:absolute;left:24px;top:256px;font-size:22px;font-weight:600}
.arrow{top:3663px;width:50px;height:48px;border-radius:4px;background:var(--orange-soft);display:flex;align-items:center;justify-content:center}
.dot{top:3678px;width:18px;height:18px;border-radius:50%}

/* footer */
.footer{left:0;top:3729px;width:1200px;height:507px;background:var(--orange-soft);color:var(--white)}
.foot-logo{left:84px;top:3832px;width:261px;height:86px;background:var(--white);display:flex;align-items:center;justify-content:center;gap:8px;font-weight:600;font-size:22px;color:var(--orange)}
.foot-tag{left:84px;top:3948px;font-size:24px;font-weight:300;line-height:34px}
.foot-col h4{font-size:21px;font-weight:600;margin-bottom:12px}
.foot-col a{display:block;font-size:18px;line-height:39px}
.social{display:flex;align-items:center;gap:18px;font-size:18px;margin-bottom:24px}
.social .ring{width:40px;height:40px;border-radius:50%;background:var(--white)}
.foot-rule{left:84px;top:4156px;width:1031px;height:1px;background:rgba(255,255,255,.85)}
.copyright{left:0;top:4172px;width:1200px;text-align:center;font-size:19px;font-weight:500}
</style>
</head>
<body>

<header class="abs nav">
  <div class="abs brand"><span class="brand-square"></span>Tallowby</div>
  <nav class="abs menu">
    <a class="active">Home</a><a>Service Area</a><a>Product</a><a>Blog</a><a>About us</a>
  </nav>
  <a class="abs login">Login</a>
</header>

<section class="abs hero" role="img" aria-label="Grey two-stall toilet trailer with folding steps parked in a factory yard"></section>
<h1 class="abs hero-title">Brighten your gathering with Tallowby Hire</h1>
<p class="abs hero-sub">We provide toilet trailer rentals at relatively cheap prices within a week. If you are interested, please contact us via the button below</p>
<a class="abs btn btn-fill">Contact us</a>
<a class="abs btn btn-line">View Product</a>

<h2 class="abs sec-title" style="top:744px">Area services that we have</h2>
<p class="abs sec-sub" style="top:803px">We have several areas available for all of you</p>
<div class="abs area" style="left:84px">Los Angeles County</div>
<div class="abs area" style="left:296px">Orange County</div>
<div class="abs area raised" style="left:510px">Riverside County</div>
<div class="abs area" style="left:723px">San Bernardino County</div>
<div class="abs area" style="left:935px">Palm Desert</div>

<div class="abs rental-band"></div>
<h2 class="abs sec-title" style="top:1200px">We provide toilet trailer rental</h2>
<p class="abs sec-sub" style="top:1258px">At low prices we provide trailer toilet facilities for you traveling to the mountains</p>

<article class="abs rental-card" style="left:84px">
  <div class="photo" role="img" aria-label="Two-stall toilet trailer with steps in a paved yard"></div>
  <div class="rc-head"><span>Trailer for 1 day rental</span><span class="price">$125</span></div>
  <div class="rc-row" style="top:1676px;top:298px"><svg width="22" height="26" viewBox="0 0 24 28"><path d="M12 1a10 10 0 0 0-10 10c0 7 10 16 10 16s10-9 10-16A10 10 0 0 0 12 1z" fill="#222"/><circle cx="12" cy="11" r="3.6" fill="#fff"/></svg>Santa Ana California</div>
  <div class="rc-row" style="top:347px"><svg width="20" height="20" viewBox="0 0 24 24"><path d="M6.6 10.8a15 15 0 0 0 6.6 6.6l2.2-2.2a1 1 0 0 1 1-.25 11.4 11.4 0 0 0 3.6.57 1 1 0 0 1 1 1V20a1 1 0 0 1-1 1A17 17 0 0 1 3 4a1 1 0 0 1 1-1h3.5a1 1 0 0 1 1 1c0 1.25.2 2.45.57 3.57a1 1 0 0 1-.25 1z" fill="#222"/></svg>+1-714-555-0142</div>
  <div class="rc-more">View More</div>
</article>

<article class="abs rental-card" style="left:641px">
  <div class="photo" role="img" aria-label="Three-stall toilet trailer with steps in a paved yard"></div>
  <div class="rc-head"><span>Trailer for 1 week rental</span><span class="price">$325</span></div>
  <div class="rc-row" style="top:298px"><svg width="22" height="26" viewBox="0 0 24 28"><path d="M12 1a10 10 0 0 0-10 10c0 7 10 16 10 16s10-9 10-16A10 10 0 0 0 12 1z" fill="#222"/><circle cx="12" cy="11" r="3.6" fill="#fff"/></svg>Santa Ana California</div>
  <div class="rc-row" style="top:347px"><svg width="20" height="20" viewBox="0 0 24 24"><path d="M6.6 10.8a15 15 0 0 0 6.6 6.6l2.2-2.2a1 1 0 0 1 1-.25 11.4 11.4 0 0 0 3.6.57 1 1 0 0 1 1 1V20a1 1 0 0 1-1 1A17 17 0 0 1 3 4a1 1 0 0 1 1-1h3.5a1 1 0 0 1 1 1c0 1.25.2 2.45.57 3.57a1 1 0 0 1-.25 1z" fill="#222"/></svg>+1-714-555-0142</div>
  <div class="rc-more">View More</div>
</article>

<h2 class="abs sec-title" style="top:1936px">Our products are for sale</h2>
<p class="abs sec-sub" style="top:2006px">We also sell various kinds of toilet equipment</p>

<article class="abs product" style="left:84px">
  <div class="photo" role="img" aria-label="White vanity sink with cabinet in a trailer washroom"></div>
  <div class="pd-head"><span>Sink</span><span>$40</span></div>
  <div class="pd-sub">Place to clean hands</div>
  <div class="pd-phone"><svg width="18" height="18" viewBox="0 0 24 24"><path d="M6.6 10.8a15 15 0 0 0 6.6 6.6l2.2-2.2a1 1 0 0 1 1-.25 11.4 11.4 0 0 0 3.6.57 1 1 0 0 1 1 1V20a1 1 0 0 1-1 1A17 17 0 0 1 3 4a1 1 0 0 1 1-1h3.5a1 1 0 0 1 1 1c0 1.25.2 2.45.57 3.57a1 1 0 0 1-.25 1z" fill="#fff"/></svg>+1-714-555-0187</div>
  <div class="pd-cta">View Product</div>
</article>
<article class="abs product raised" style="left:442px">
  <div class="photo" role="img" aria-label="White toilet inside a compact trailer washroom"></div>
  <div class="pd-head"><span>Toilet</span><span>$80</span></div>
  <div class="pd-sub">Place to clean hands</div>
  <div class="pd-phone"><svg width="18" height="18" viewBox="0 0 24 24"><path d="M6.6 10.8a15 15 0 0 0 6.6 6.6l2.2-2.2a1 1 0 0 1 1-.25 11.4 11.4 0 0 0 3.6.57 1 1 0 0 1 1 1V20a1 1 0 0 1-1 1A17 17 0 0 1 3 4a1 1 0 0 1 1-1h3.5a1 1 0 0 1 1 1c0 1.25.2 2.45.57 3.57a1 1 0 0 1-.25 1z" fill="#fff"/></svg>+1-714-555-0187</div>
  <div class="pd-cta">View Product</div>
</article>
<article class="abs product" style="left:799px">
  <div class="photo warm" role="img" aria-label="Bathroom with stone wall, bathtub and wood panelling"></div>
  <div class="pd-head"><span>Bathroom facilities</span><span>$99</span></div>
  <div class="pd-sub">Place to clean hands</div>
  <div class="pd-phone"><svg width="18" height="18" viewBox="0 0 24 24"><path d="M6.6 10.8a15 15 0 0 0 6.6 6.6l2.2-2.2a1 1 0 0 1 1-.25 11.4 11.4 0 0 0 3.6.57 1 1 0 0 1 1 1V20a1 1 0 0 1-1 1A17 17 0 0 1 3 4a1 1 0 0 1 1-1h3.5a1 1 0 0 1 1 1c0 1.25.2 2.45.57 3.57a1 1 0 0 1-.25 1z" fill="#fff"/></svg>+1-714-555-0187</div>
  <div class="pd-cta">View Product</div>
</article>

<div class="abs about-photo" role="img" aria-label="Business team reviewing documents and a tablet at a desk"></div>
<h2 class="abs about-title">About us</h2>
<p class="abs about-text">We provide toilet trailer rentals from 1 day to 1 week with cheap prices and benefits if you subscribe now with us</p>
<div class="abs tick-row" style="top:2914px"><svg width="32" height="32" viewBox="0 0 32 32"><path d="M16 1l4 3 5-.5 1.5 4.8 4.5 2.7-1.5 4.9 1.5 4.9-4.5 2.7-1.5 4.8-5-.5-4 3-4-3-5 .5-1.5-4.8L1 21.6l1.5-4.9L1 11.8l4.5-2.7L7 4.3l5 .5z" fill="#2f2f2f"/><path d="M10 16.5l4 4 8-8" stroke="#fff" stroke-width="2.6" fill="none" stroke-linecap="round" stroke-linejoin="round"/></svg>Get a very luxurious toilet</div>
<div class="abs tick-row" style="top:2967px"><svg width="32" height="32" viewBox="0 0 32 32"><path d="M16 1l4 3 5-.5 1.5 4.8 4.5 2.7-1.5 4.9 1.5 4.9-4.5 2.7-1.5 4.8-5-.5-4 3-4-3-5 .5-1.5-4.8L1 21.6l1.5-4.9L1 11.8l4.5-2.7L7 4.3l5 .5z" fill="#2f2f2f"/><path d="M10 16.5l4 4 8-8" stroke="#fff" stroke-width="2.6" fill="none" stroke-linecap="round" stroke-linejoin="round"/></svg>Get beautiful views and clean water</div>
<div class="abs tick-row" style="top:3020px"><svg width="32" height="32" viewBox="0 0 32 32"><path d="M16 1l4 3 5-.5 1.5 4.8 4.5 2.7-1.5 4.9 1.5 4.9-4.5 2.7-1.5 4.8-5-.5-4 3-4-3-5 .5-1.5-4.8L1 21.6l1.5-4.9L1 11.8l4.5-2.7L7 4.3l5 .5z" fill="#2f2f2f"/><path d="M10 16.5l4 4 8-8" stroke="#fff" stroke-width="2.6" fill="none" stroke-linecap="round" stroke-linejoin="round"/></svg>Camping becomes fun with a mobile toilet</div>
<div class="abs tick-row" style="top:3073px"><svg width="32" height="32" viewBox="0 0 32 32"><path d="M16 1l4 3 5-.5 1.5 4.8 4.5 2.7-1.5 4.9 1.5 4.9-4.5 2.7-1.5 4.8-5-.5-4 3-4-3-5 .5-1.5-4.8L1 21.6l1.5-4.9L1 11.8l4.5-2.7L7 4.3l5 .5z" fill="#2f2f2f"/><path d="M10 16.5l4 4 8-8" stroke="#fff" stroke-width="2.6" fill="none" stroke-linecap="round" stroke-linejoin="round"/></svg>Cheap prices for you and your friends</div>

<h2 class="abs sec-title" style="top:3232px">Very happy client with this rental</h2>

<article class="abs review" style="left:84px">
  <div class="avatar" role="img" aria-label="Client portrait"></div>
  <div class="rv-name">Delvane</div>
  <p class="rv-quote">“We enjoyed renting it so much that we suggested to our friends to rent or buy things here”</p>
  <div class="rv-time">2 years ago</div>
</article>
<article class="abs review" style="left:442px">
  <div class="avatar" role="img" aria-label="Client portrait"></div>
  <div class="rv-name">Marlo</div>
  <p class="rv-quote">“We enjoyed renting it so much that we suggested to our friends to rent or buy things here”</p>
  <div class="rv-time">1 years ago</div>
</article>
<article class="abs review" style="left:799px">
  <div class="avatar" role="img" aria-label="Client portrait"></div>
  <div class="rv-name">Quennie</div>
  <p class="rv-quote">“We enjoyed renting it so much that we suggested to our friends to rent or buy things here”</p>
  <div class="rv-time">2 years ago</div>
</article>

<div class="abs arrow" style="left:350px"><svg width="16" height="16" viewBox="0 0 16 16"><path d="M10 3L5 8l5 5" stroke="#fff" stroke-width="2.2" fill="none" stroke-linecap="round" stroke-linejoin="round"/></svg></div>
<div class="abs dot" style="left:575px;background:var(--orange-soft)"></div>
<div class="abs dot" style="left:605px;background:var(--peach)"></div>
<div class="abs arrow" style="left:799px"><svg width="16" height="16" viewBox="0 0 16 16"><path d="M6 3l5 5-5 5" stroke="#fff" stroke-width="2.2" fill="none" stroke-linecap="round" stroke-linejoin="round"/></svg></div>

<footer class="abs footer"></footer>
<div class="abs foot-logo"><span class="brand-square"></span>Tallowby</div>
<p class="abs foot-tag" style="color:#fff">Brighten your gathering with<br>Tallowby Hire</p>
<div class="abs foot-col" style="left:567px;top:3832px;color:#fff">
  <h4>Info</h4><a>Home</a><a>Product</a><a>Service</a><a>About us</a>
</div>
<div class="abs foot-col" style="left:717px;top:3832px;color:#fff">
  <h4>Company</h4><a>Galery</a><a>News</a><a>Contact us</a><a>Connect</a>
</div>
<div class="abs foot-col" style="left:870px;top:3830px;color:#fff">
  <h4>Find us on social media</h4>
  <div class="social"><span class="ring"></span>Kinfeed</div>
  <div class="social"><span class="ring"></span>Pictora</div>
  <div class="social"><span class="ring"></span>Chirplet</div>
</div>
<div class="abs foot-rule"></div>
<p class="abs copyright" style="color:#fff">All Right Reserved / Privacy Policy / Termn and use</p>

</body>
</html>
```